Business Card Design for Flood Rescue 360 - Property Restoration Professionals

I need a business card designed for Flood Rescue 360. We are a full-service property restoration solution. Providing water, fire, smoke & storm restoration as well as mold remediation and full remodel or reconstruction to homes and businesses across Dallas-Fort Worth, TX.
Target Market(s)
home and business owners with insurance covered property damage from water, fire or storm related damage
Industry/Entity Type
property restoration
Contact Information for Business Card
Marcus Pelley General Manager Cell: 214-555-0193 Office: 469-555-0148 email: Marcus@FloodRescue360.example services: Water, Fire, Mold, Reconstruction Tagline: Urgency for Your Water Emergency!
Look and feel
Each slider illustrates characteristics of the customer's brand and the style your logo design should communicate.

```html
<!DOCTYPE html>
<html lang="en">
<head>
<meta charset="utf-8">
<title>Flood Rescue 360 – Business Card</title>
<link rel="stylesheet" href="https://fonts.googleapis.com/css2?family=Montserrat:wght@400;500;800&display=swap">
<style>
  :root {
    --backdrop: #474747;
    --card: #181818;
    --card-deep: #121212;
    --brand-blue: #11a9e2;
    --text-light: #f2f2f2;
    --pattern-dark: #202020;
    --pattern-mid: #2c2c2c;
  }
  * { box-sizing: border-box; margin: 0; padding: 0; }
  html, body {
    width: 1200px; height: 801px; overflow: hidden;
    background: var(--backdrop);
    font-family: "Montserrat", sans-serif;
  }
  .stage {
    position: relative; width: 1200px; height: 801px;
    display: flex; align-items: center; justify-content: center; gap: 48px;
  }
  .card {
    position: relative; width: 532px; height: 304px;
    background: var(--card);
    border-bottom: 3px solid var(--brand-blue);
    box-shadow: 0 18px 40px rgba(0,0,0,.35);
    overflow: hidden;
  }
  /* front */
  .company-name {
    position: absolute; left: 28px; top: 168px; width: 200px;
    color: var(--text-light); font-weight: 500; font-size: 20px;
    line-height: 1.2; white-space: nowrap;
  }
  .divider {
    position: absolute; left: 240px; top: 112px; width: 2px; height: 138px;
    background: var(--brand-blue);
  }
  .person {
    position: absolute; left: 258px; top: 34px; right: 18px;
  }
  .person-name { color: var(--brand-blue); font-weight: 800; font-size: 25px; line-height: 1.2; }
  .person-title { color: var(--text-light); font-size: 12px; margin-top: 2px; }
  .tagline { color: var(--text-light); font-size: 12px; margin-top: 14px; }
  .contact-list { list-style: none; margin-top: 12px; }
  .contact-list li {
    display: flex; align-items: center; gap: 8px;
    color: var(--text-light); font-size: 12.5px; line-height: 21px;
  }
  .contact-list svg { width: 12px; height: 12px; flex: none; fill: var(--brand-blue); }
  .services {
    position: absolute; left: 258px; bottom: 20px; right: 14px;
  }
  .services-heading {
    color: var(--brand-blue); font-weight: 800; font-size: 18px; letter-spacing: .5px;
  }
  .services-list {
    display: flex; align-items: center; gap: 7px; white-space: nowrap;
    color: var(--text-light); font-size: 13.5px; margin-top: 2px;
  }
  .services-list .dot {
    flex: none; width: 5px; height: 5px; border-radius: 50%; background: var(--brand-blue);
  }
  /* back */
  .card-back { background: var(--card-deep); }
  .pattern-field {
    position: absolute; inset: 0;
    background: linear-gradient(120deg, var(--pattern-mid) 0%, var(--pattern-dark) 45%, var(--card-deep) 100%);
  }
  .back-company-name {
    position: absolute; left: 0; right: 0; top: 50%; transform: translateY(-50%);
    text-align: center; color: var(--text-light);
    font-weight: 500; font-size: 24px; line-height: 1.2;
  }
</style>
</head>
<body>
<main class="stage">
  <section class="card card-front" aria-label="Business card front">
    <p class="company-name">Flood Rescue 360</p>
    <div class="divider"></div>
    <div class="person">
      <h1 class="person-name">Marcus Pelley</h1>
      <p class="person-title">General Manager</p>
      <p class="tagline">Urgency for Your Water Emergency!</p>
      <ul class="contact-list">
        <li><svg viewBox="0 0 12 12" aria-hidden="true"><path d="M3 0h6a1 1 0 0 1 1 1v10a1 1 0 0 1-1 1H3a1 1 0 0 1-1-1V1a1 1 0 0 1 1-1zm0 1.5v8h6v-8z"/></svg>214-555-0193</li>
        <li><svg viewBox="0 0 12 12" aria-hidden="true"><path d="M1 4c3-3 7-3 10 0l-1.5 1.5-2-1V3.5h-3v1l-2 1zM2 7h8l1 4H1z"/></svg>469-555-0148</li>
        <li><svg viewBox="0 0 12 12" aria-hidden="true"><path d="M0 2h12v8H0zm1 1v.4l5 3.2 5-3.2V3zm0 1.6V9h10V4.6L6 7.8z"/></svg>Marcus@FloodRescue360.example</li>
        <li><svg viewBox="0 0 12 12" aria-hidden="true"><circle cx="6" cy="6" r="6"/></svg>FloodRescue360.example</li>
      </ul>
    </div>
    <div class="services">
      <h2 class="services-heading">SERVICES</h2>
      <p class="services-list">Water<span class="dot"></span>Fire<span class="dot"></span>Mold<span class="dot"></span>Reconstruction</p>
    </div>
  </section>

  <section class="card card-back" aria-label="Business card back">
    <div class="pattern-field" role="img" aria-label="Repeating tone-on-tone brand pattern in dark grey gloss"></div>
    <p class="back-company-name">Flood Rescue 360</p>
  </section>
</main>
</body>
</html>
```